Audio Visual company needs WordPress Site re-design

We need a new, simple and sleek redesign of our website, www.kelvarosupply.net. It is crucial that it is mobile platform friendly! The company emphasis is on commercial sound and video installation.

Examples of what our company does can be found here: http://bramwickav.org/

I am NOT looking for a storefront or an e-commerce site. I would just like an elegant site that describes our services. Perhaps incorporate a sleek showcase into the homepage of projects we have completed. Also would like an elegant menu-bar, perhaps enhance our current site menu or similar.

Here is a link to another site that exhibits the content I am looking for. Their target market is also much like mine.
http://www.pollanderhouse.com/ ........ A polished up version of this site would probably be my ideal site. It has almost EXACTLY the content I am looking for. Exclude the "Printing & signage" category. Needs nicer menus, contact page and project showcase.

Here is another example: http://www.clearhavenmedia.com/ ......... This site has a very nice homepage design with a good layout and feature slider. The site is simple, elegant and to the point.

Target Market(s)

Corporate/commercial business, Educational institutions

Industry/Entity Type

E-Commerce

Font styles to use
Serif
Sans Serif

Requirements
Must have
• Mobile friendly navigation
Nice to have
• HTML5 & CSS3
Should not have
• No Adobe Flash content. No store templates or e-commerce. We are a service based company not a product sales company

```html
<!DOCTYPE html>
<html lang="en">
<head>
<meta charset="utf-8">
<title>Kelvaro Supply — Sound &amp; Video Solutions</title>
<link href="https://fonts.googleapis.com/css2?family=Open+Sans:wght@400;600;700&display=swap" rel="stylesheet">
<style>
:root{
  --navy:#1b2a55;
  --red:#b3151b;
  --text:#555;
  --dark:#222;
  --light:#f1f1f1;
  --line:#e4e4e4;
  --footer:#000;
  --link-blue:#3b8fd6;
}
*{box-sizing:border-box;margin:0;padding:0}
html,body{width:673px;height:1200px;overflow:hidden}
body{font-family:"Open Sans",Arial,sans-serif;color:var(--text);background:#fff;position:relative}
.site-header{position:absolute;top:0;left:0;width:673px;height:48px;background:#fff}
.brand{position:absolute;left:33px;top:14px;display:flex;align-items:center;gap:6px;font-weight:700;font-size:14px;color:var(--navy);letter-spacing:.3px}
.brand-mark{width:10px;height:10px;background:var(--red)}
.main-nav{position:absolute;right:34px;top:17px;display:flex;gap:0}
.main-nav a{font-size:7.5px;color:#444;text-decoration:none;padding:3px 13px;border:1px solid transparent}
.main-nav a.active{border-color:#333}
.hero{position:absolute;top:48px;left:0;width:673px;height:310px;
  background:radial-gradient(circle at 30% 30%,#c44fc9 0,transparent 25%),radial-gradient(circle at 75% 70%,#f0a531 0,transparent 22%),radial-gradient(circle at 88% 25%,#f36b5b 0,transparent 20%),linear-gradient(135deg,#5a3a6e,#2e2440 55%,#8b5a4a)}
.hero-arrow{position:absolute;top:142px}
.hero-arrow.prev{left:16px}.hero-arrow.next{right:16px}
.welcome{position:absolute;top:372px;left:0;width:673px;text-align:center}
.section-title{font-size:11px;font-weight:700;color:var(--navy);text-transform:uppercase}
.welcome p{font-size:7.5px;line-height:12.5px;width:510px;margin:9px auto 0;color:var(--text)}
.btn-solid{display:inline-block;margin-top:12px;background:var(--navy);color:#fff;font-size:7.5px;padding:5px 13px;border-radius:2px}
.features{position:absolute;top:490px;left:0;width:673px;height:268px;background:var(--light)}
.features .section-title{position:absolute;top:15px;width:100%;text-align:center}
.card{position:absolute;top:43px;width:174px;height:209px;background:#fff;text-align:center;box-shadow:0 6px 6px -6px rgba(0,0,0,.25)}
.card-photo{height:104px}
.card h3{font-size:8px;font-weight:700;color:var(--red);text-transform:uppercase;line-height:13px;margin:9px 12px 0}
.card p{font-size:7px;line-height:12px;margin:0 12px;text-align:justify;text-align-last:center}
.btn-outline{display:inline-block;margin-top:8px;border:1px solid var(--red);color:var(--red);font-size:7px;padding:4px 7px;border-radius:1px}
.testimonials{position:absolute;top:776px;left:48px;width:259px;height:219px;border:1px solid var(--line);background:#fff}
.testimonials .section-title{text-align:center;margin-top:9px;font-weight:600;font-size:11px;color:#222}
.testimonial-photo{position:absolute;left:20px;top:32px;width:218px;height:101px;background:linear-gradient(90deg,#4f6b3a,#9bb189 55%,#6f8f5a)}
.quote-mark{position:absolute;left:19px;top:144px}
.quote-name{position:absolute;left:44px;top:148px;font-size:7.5px;color:#222}
.quote-text{position:absolute;left:44px;top:160px;width:200px;font-size:7px;line-height:12px}
.quote-author{position:absolute;left:44px;top:201px;font-size:7.5px;color:#222}
.dots{position:absolute;right:24px;top:206px;display:flex;gap:2px}
.dots i{width:4px;height:4px;border-radius:50%;background:#222}
.dots i:first-child{background:var(--red)}
.project{position:absolute;width:147px;height:105px}
.project span{position:absolute;bottom:5px;left:0;width:100%;text-align:center;color:#fff;font-size:7px;letter-spacing:.3px;text-transform:uppercase}
.site-footer{position:absolute;top:1016px;left:0;width:673px;height:184px;background:var(--footer);color:#fff}
.footer-col{position:absolute;top:12px}
.footer-col h4{font-size:7.5px;font-weight:400;text-transform:uppercase;margin-bottom:14px}
.link-list{list-style:none}
.link-list li{font-size:7px;margin-bottom:8px;padding-left:14px;position:relative}
.link-list li::before{content:"›";position:absolute;left:0;top:-2px;font-size:9px}
.post{font-size:7px;line-height:10px;width:151px;text-align:justify;margin-bottom:8px}
.post small{display:block;color:var(--link-blue);font-size:6.5px}
.blog-item{display:flex;gap:8px;margin-bottom:14px}
.blog-thumb{width:54px;height:39px;border:1px solid #555}
.blog-item h5{font-size:7px;font-weight:600;margin-bottom:2px}
.blog-item p{font-size:6.5px;line-height:10px;width:112px}
.blog-item a{font-size:6.5px;color:var(--red);text-decoration:none}
.contact-row{display:flex;align-items:center;gap:8px;font-size:7px;margin-bottom:8px}
.social{display:flex;gap:3px;margin-top:5px}
.social i{width:12px;height:12px;background:#fff;border-radius:2px}
.copyright{position:absolute;bottom:12px;width:100%;text-align:center;font-size:7px}
</style>
</head>
<body>
<header class="site-header">
  <div class="brand"><span class="brand-mark"></span>KELVARO SUPPLY</div>
  <nav class="main-nav">
    <a class="active">Home</a><a>About us</a><a>Services</a><a>Contact us</a><a>Customer Review</a>
  </nav>
</header>

<section class="hero" role="img" aria-label="Concert crowd, hand holding a phone filming a stage with colourful bokeh lights">
  <svg class="hero-arrow prev" width="20" height="20" viewBox="0 0 20 20"><circle cx="10" cy="10" r="9" fill="#888" fill-opacity=".7"/><path d="M12 5 7 10l5 5" stroke="#333" stroke-width="2.5" fill="none"/></svg>
  <svg class="hero-arrow next" width="20" height="20" viewBox="0 0 20 20"><circle cx="10" cy="10" r="9" fill="#888" fill-opacity=".7"/><path d="M8 5l5 5-5 5" stroke="#333" stroke-width="2.5" fill="none"/></svg>
</section>

<section class="welcome">
  <h1 class="section-title">Welcome to Kelvaro Supply</h1>
  <p>"Lorem ipsum dolor sit amet, consectetur adipiscing elit, sed do eiusmod tempor incididunt ut labore et dolore magna aliqua. Ut enim ad minim veniam, quis nostrud exercitation ullamco laboris nisi ut aliquip ex ea commodo consequat. Duis aute irure dolor in reprehenderit in voluptate velit esse cillum dolore eu fugiat nulla pariatur. Excepteur sint occaecat cupidatat non proident,</p>
  <span class="btn-solid">READ MORE</span>
</section>

<section class="features">
  <h2 class="section-title">Our Features</h2>
  <article class="card" style="left:47px">
    <div class="card-photo" role="img" aria-label="Audio mixing console under purple light" style="background:linear-gradient(135deg,#5b3f7a,#b38fd0 50%,#7a2f4f)"></div>
    <h3>Installation of Commercial Sound System</h3>
    <p>perspiciatis unde omnis iste natus error sit voluptatem accusantium doloremque laudantium, totam rem aperiam</p>
    <span class="btn-outline">READ MORE</span>
  </article>
  <article class="card" style="left:249px">
    <div class="card-photo" role="img" aria-label="Widescreen monitor glowing on a dark background" style="background:radial-gradient(circle at 70% 60%,#c9876a 0,#2a2a35 30%,#0c0c10 70%)"></div>
    <h3 style="margin-top:14px;margin-bottom:7px">HD Video Displays</h3>
    <p>perspiciatis unde omnis iste natus error sit voluptatem accusantium doloremque laudantium, totam rem aperiam</p>
    <span class="btn-outline">READ MORE</span>
  </article>
  <article class="card" style="left:451px">
    <div class="card-photo" role="img" aria-label="Film strip and clapperboard on black" style="background:linear-gradient(135deg,#1a1a1a,#555 45%,#111)"></div>
    <h3>Digital Projection and Digital Signage</h3>
    <p>perspiciatis unde omnis iste natus error sit voluptatem accusantium doloremque laudantium, totam rem aperiam</p>
    <span class="btn-outline">READ MORE</span>
  </article>
</section>

<section class="testimonials">
  <h2 class="section-title">TESTIMONIALS</h2>
  <div class="testimonial-photo" role="img" aria-label="Businessman in shirt and tie holding a tablet outdoors"></div>
  <svg class="quote-mark" width="20" height="16" viewBox="0 0 20 16"><path d="M0 16V8Q0 1 8 0v3Q4 4 4 8h4v8zM11 16V8q0-7 8-8v3q-4 1-4 5h4v8z" fill="var(--red)"/></svg>
  <div class="quote-name">IPSUM DOLOR</div>
  <p class="quote-text">"Lorem ipsum dolor sit amet, consectetur adipiscing elit, sed do eiusmod tempor incididunt ut labore et dolore magna aliqua.</p>
  <div class="quote-author">Martin</div>
  <div class="dots"><i></i><i></i><i></i><i></i></div>
</section>

<div class="project" style="left:324px;top:777px;background:linear-gradient(180deg,#222,#1f5fc4 40%,#2a2a2a)" role="img" aria-label="Two large wall-mounted blue displays"><span>Dual 70-inch displays</span></div>
<div class="project" style="left:478px;top:777px;background:linear-gradient(180deg,#4a3a30,#7a6a5a 40%,#3a2a20)" role="img" aria-label="Row of menu display screens above a counter"><span>Multi-display digital boards</span></div>
<div class="project" style="left:324px;top:890px;background:linear-gradient(90deg,#1a2240,#c8c8c8 40%,#ddd 60%,#1a2240)" role="img" aria-label="Auditorium with projection screens and curtains"><span>Auditorium</span></div>
<div class="project" style="left:478px;top:890px;background:linear-gradient(180deg,#333 0,#eee 8%,#f2f2f2 85%,#222)" role="img" aria-label="Interactive whiteboard mounted on a wall"><span>Lumera interactive boards</span></div>

<footer class="site-footer">
  <div class="footer-col" style="left:36px">
    <h4>Links</h4>
    <ul class="link-list"><li>Home</li><li>About us</li><li>Services</li><li>Contact us</li><li>Customer Review</li></ul>
  </div>
  <div class="footer-col" style="left:144px">
    <h4>Latest Post</h4>
    <p class="post">consectetur adipiscing elit, sed do eiusmod tempor incididunt ut labore et dolore magna aliqua.<small>1 day ago</small></p>
    <p class="post">consectetur adipiscing elit, sed do eiusmod tempor incididunt ut labore et dolore magna aliqua.<small>1 day ago</small></p>
  </div>
  <div class="footer-col" style="left:334px">
    <h4>Latest from the Blog</h4>
    <div class="blog-item">
      <div class="blog-thumb" role="img" aria-label="Stage performance with coloured lights" style="background:linear-gradient(135deg,#3a2a6a,#c58ad0)"></div>
      <div><h5>IPSUM DOLOR</h5><p>sed do eiusmod tempor incididunt ut labore et dolore magna aliqua.</p><a>Read More &gt;&gt;</a></div>
    </div>
    <div class="blog-item">
      <div class="blog-thumb" role="img" aria-label="Presenter beside a large video wall" style="background:linear-gradient(135deg,#1e3a2a,#5a8a5a)"></div>
      <div><h5>IPSUM DOLOR</h5><p>sed do eiusmod tempor incididunt ut labore et dolore magna aliqua.</p><a>Read More &gt;&gt;</a></div>
    </div>
  </div>
  <div class="footer-col" style="left:545px">
    <h4 style="margin-bottom:10px">Contact Us</h4>
    <div class="contact-row"><svg width="13" height="10" viewBox="0 0 13 10"><rect x=".5" y=".5" width="12" height="9" fill="none" stroke="#fff"/><path d="M.5.5l6 5 6-5" fill="none" stroke="#fff"/></svg>info@kelvarosupply.net</div>
    <div class="contact-row"><svg width="13" height="13" viewBox="0 0 13 13"><rect width="13" height="13" rx="2" fill="#fff"/><path d="M4 3l1.5 2-1 1q1 2 2.5 2.5l1-1 2 1.5-1 1.5Q6 10.5 3 4z" fill="#000"/></svg>(773) 555-0148</div>
    <h4 style="margin:10px 0 0">Follow Us</h4>
    <div class="social"><i></i><i></i><i></i><i></i><i></i></div>
  </div>
  <p class="copyright">Kelvaro Supply © 2015 privacy policy</p>
</footer>
</body>
</html>
```